Basic business card

use my newly created logo - and the phrases (Leaner Test Budgets & Faster Silicon Launch Cycles) - and my new email domain / ID - use at conferences / tradeshows

Industry/Entity Type

semiconductor

Contact Information for Business Card

Daniel K Forde, Owner, communicate via Logo - Lower COT - Cost of Test, Accelerated NPI - New Product Introduction, phone +1 555 613 0946, Corvale, Nevada, USA, daniel.forde@qal-vub.com

Font styles to use
Sans Serif

Requirements
Nice to have
• re-use my logo created via Pixel Harbor last August (#7315926)

```html
<!DOCTYPE html>
<html lang="en">
<head>
<meta charset="utf-8">
<title>QAL-VUB Business Card</title>
<link rel="stylesheet" href="https://fonts.googleapis.com/css2?family=Marcellus&family=Montserrat:wght@400;500;700&display=swap">
<style>
  :root {
    --backdrop: #cdd1d3;
    --paper: #f7f8f8;
    --ink-navy: #1c2541;
    --brand-blue: #1f5aa6;
    --edge-blue: #1d4a9c;
    --text-grey: #3a3f4a;
    --icon-orange: #e0792a;
    --icon-green: #5aa02c;
  }
  * { box-sizing: border-box; margin: 0; padding: 0; }
  html, body {
    width: 1200px; height: 829px; overflow: hidden;
    background: var(--backdrop);
  }
  .canvas {
    position: relative; width: 1200px; height: 829px;
    display: flex; align-items: center; justify-content: center; gap: 40px;
  }
  .card {
    position: relative; width: 540px; height: 309px;
    background: var(--paper);
    border-bottom: 5px solid var(--edge-blue);
    box-shadow: 0 14px 30px rgba(0,0,0,0.18);
    overflow: hidden;
  }
  .brand-name {
    font-family: "Marcellus", serif;
    color: var(--ink-navy);
    letter-spacing: 0.02em;
    display: flex; align-items: center;
    white-space: nowrap;
  }
  .brand-mark { display: inline-block; background: var(--brand-blue); }

  /* contact side */
  .card-contact .brand-name {
    position: absolute; left: 40px; top: 34px; font-size: 34px; gap: 12px;
  }
  .card-contact .brand-mark { width: 14px; height: 14px; }
  .identity {
    position: absolute; left: 0; top: 112px;
    padding-left: 44px;
  }
  .identity::before {
    content: ""; position: absolute; left: 0; top: 2px;
    width: 16px; height: 34px; background: var(--brand-blue);
  }
  .person-name {
    font-family: "Montserrat", sans-serif; font-weight: 700;
    font-size: 22px; color: var(--ink-navy);
  }
  .person-role {
    font-family: "Montserrat", sans-serif; font-weight: 400;
    font-size: 13px; color: var(--text-grey); margin-top: 2px;
  }
  .contact-list {
    position: absolute; left: 44px; top: 182px; list-style: none;
    font-family: "Montserrat", sans-serif; font-size: 14px; color: var(--text-grey);
  }
  .contact-list li { display: flex; align-items: center; gap: 9px; margin-bottom: 9px; white-space: nowrap; }
  .contact-list svg { width: 13px; height: 13px; flex: none; }

  /* brand side */
  .card-brand { display: flex; flex-direction: column; align-items: center; justify-content: center; }
  .card-brand .brand-name { font-size: 60px; gap: 18px; }
  .card-brand .brand-mark { width: 22px; height: 22px; }
  .tagline {
    margin-top: 22px;
    font-family: "Montserrat", sans-serif; font-weight: 400;
    font-size: 14.5px; color: var(--brand-blue); letter-spacing: 0.03em;
    white-space: nowrap;
  }
</style>
</head>
<body>
<main class="canvas">
  <section class="card card-contact">
    <div class="brand-name"><span class="brand-mark"></span>QAL-VUB</div>
    <div class="identity">
      <p class="person-name">Daniel K Forde</p>
      <p class="person-role">Owner</p>
    </div>
    <ul class="contact-list">
      <li>
        <svg viewBox="0 0 16 16" aria-hidden="true"><path fill="var(--icon-orange)" d="M4 1l3 3-2 2c1 2 3 4 5 5l2-2 3 3-2 3C7 15 1 9 1 3z"/></svg>
        +1 555 613 0946
      </li>
      <li>
        <svg viewBox="0 0 16 16" aria-hidden="true"><rect x="1" y="3" width="14" height="10" fill="var(--brand-blue)"/><path d="M1 3l7 6 7-6" stroke="#fff" stroke-width="1.4" fill="none"/></svg>
        daniel.forde@qal-vub.com
      </li>
      <li>
        <svg viewBox="0 0 16 16" aria-hidden="true"><path fill="var(--icon-green)" d="M8 1a5 5 0 0 1 5 5c0 4-5 9-5 9S3 10 3 6a5 5 0 0 1 5-5z"/><circle cx="8" cy="6" r="2" fill="#fff"/></svg>
        Corvale, Nevada, USA
      </li>
    </ul>
  </section>

  <section class="card card-brand">
    <div class="brand-name"><span class="brand-mark"></span>QAL-VUB</div>
    <p class="tagline">Leaner Test Budgets &amp; Faster Silicon Launch Cycles</p>
  </section>
</main>
</body>
</html>
```